CalmPeak Nurses' Manifesto

Design a manifesto to inspire and motivate nurses to work at minimum standards of excellence in their nursing practice.

The manifesto will become a feature of our website, at conferences, workshops and retreats. It will also be featured on other marketing tools.

Primary Market:
Nurses and/or other healthcare professionals (specifically Doctors, Occupational Therapists, Psychologists and Social Workers).

However the manifesto is equally applicable to all nurses and healthcare professionals from new graduates to very experienced senior clinicians, administration officers,managers and healthcare executive personnel.

Mainly females and primarily 35 to 65 years old, which suggests people in this target age group have extensive experience, but have become jaded'.

The purpose of our business is to assist healthcare professionals, primarily nurses, to maintain their enthusiasm and excellence in service provision, for their benefit as well as the benefit of the clients.

I have attached:
File 1: Copy Samples and examples: which has the copy for the manifesto, examples that appeal to us and our 3 attempts.
File 2: Our colour Spec Sheet, HOWEVER the colours are not necessary limited to these colours. These colours are not in the logo that will be on the manifesto. The colours on the logo attached can/or also be used.
File 3: Prototype logo. The final logo will be available within 3 to 4 days.

Industry/Entity Type

Healthcare

Requirements
Must have
• Must use the copy as per the attached file.

It should be contemporary, eye catching and motivational.

Should not have
• MUST BE EASY TO READ. Each line MUST be clearly defined from each other.

```html
<!DOCTYPE html>
<html lang="en">
<head>
<meta charset="utf-8">
<title>CalmPeak Nurses' Manifesto</title>
<link href="https://fonts.googleapis.com/css2?family=Arimo:ital,wght@0,400;0,700;1,700&family=Oswald:wght@200&display=swap" rel="stylesheet">
<style>
  :root{
    --page:#ffffff;
    --edge:#d62bd6;
    --band:#3ba7a3;
    --band-type:#86d3cf;
    --ink:#444444;
    --teal:#2a9b97;
    --green:#5f9f35;
    --lime:#9cc43c;
    --star:#a9abad;
    --badge-top:#f4f4f4;
    --badge-bottom:#d9dadb;
    --shadow:#b9b9b9;
  }
  *{margin:0;padding:0;box-sizing:border-box}
  html,body{width:874px;height:1200px;overflow:hidden;background:var(--page)}
  .sheet{
    position:relative;width:874px;height:1200px;background:var(--page);
    border-top:2px solid var(--edge);border-left:2px solid var(--edge);border-bottom:2px solid var(--edge);
    font-family:"Arimo",Arial,sans-serif;
  }
  .side-band{
    position:absolute;left:630px;top:44px;width:202px;height:1154px;background:var(--band);
    box-shadow:8px 0 0 var(--shadow);
  }
  .side-band__name{
    position:absolute;left:101px;top:540px;width:1000px;
    transform:translate(-50%,-50%) rotate(-90deg);
    font-family:"Oswald",sans-serif;font-weight:200;font-size:96px;letter-spacing:1px;
    color:var(--band-type);text-align:center;white-space:nowrap;line-height:1;
  }
  .brand{
    position:absolute;left:70px;top:80px;width:200px;text-align:center;
  }
  .brand__dot{display:block;width:96px;height:96px;margin:0 auto 14px;border-radius:50%;background:var(--teal)}
  .brand__name{font-family:"Arimo",Arial,sans-serif;font-weight:400;font-size:25px;line-height:1.05;color:#555}
  .content{
    position:absolute;left:92px;top:344px;width:536px;
    display:flex;flex-direction:column;
  }
  .title{
    font-family:"Arimo",Arial,sans-serif;font-style:italic;font-weight:700;font-size:44px;line-height:1.2;color:var(--green);
    margin:0 0 10px 2px;
  }
  .title__accent{color:var(--lime)}
  .manifesto{
    font-style:italic;font-weight:700;font-size:17.5px;line-height:25px;
  }
  .manifesto__lead{font-size:21px;line-height:1}
  .manifesto__big{font-size:29px;line-height:1}
  .star{display:inline-block;width:14px;height:14px;margin:0 4px 0 7px;vertical-align:-1px}
  .c-ink{color:var(--ink)} .c-teal{color:var(--teal)} .c-green{color:var(--green)} .c-lime{color:var(--lime)}
  .u{text-decoration:underline}
  .closing{
    margin:22px 0 0 14px;
    font-style:italic;font-weight:700;font-size:31px;line-height:1.2;color:var(--green);
  }
  .closing .star{width:22px;height:22px;margin-left:0}
  .partner-badge{
    position:absolute;left:636px;top:1030px;width:168px;height:128px;
    background:linear-gradient(180deg,var(--badge-top),var(--badge-bottom));
    display:flex;align-items:center;justify-content:center;
  }
  .partner-badge__name{font-family:"Arimo",Arial,sans-serif;font-weight:700;font-size:26px;color:var(--teal)}
</style>
</head>
<body>
<svg width="0" height="0" style="position:absolute">
  <defs>
    <symbol id="sparkle" viewBox="0 0 20 20">
      <path d="M10 0 L12.2 7.8 L20 10 L12.2 12.2 L10 20 L7.8 12.2 L0 10 L7.8 7.8 Z" fill="#a9abad"/>
    </symbol>
  </defs>
</svg>
<main class="sheet">
  <div class="side-band">
    <div class="side-band__name">BRIGHT WARD STUDIO</div>
  </div>

  <header class="brand">
    <span class="brand__dot"></span>
    <p class="brand__name">Bright Ward<br>Studio</p>
  </header>

  <section class="content">
    <h1 class="title">Nurses’ <span class="title__accent">Manifesto</span></h1>

    <p class="manifesto">
      <svg class="star"><use href="#sparkle"/></svg><span class="c-ink manifesto__lead">Nurse with open hands, hearts and minds.</span>
      <svg class="star"><use href="#sparkle"/></svg><span class="c-teal">Look after yourself and value your health as much as you value the health of others.</span>
      <svg class="star"><use href="#sparkle"/></svg><span class="c-lime">Delight your clients and colleagues by exceeding their expectations.</span>
      <svg class="star"><use href="#sparkle"/></svg><span class="c-teal manifesto__lead">Deliver care <span class="u">skilfully</span>.</span>
      <svg class="star"><use href="#sparkle"/></svg><span class="c-ink">Respect the limits of other people’s knowledge and share your knowledge generously.</span>
      <svg class="star"><use href="#sparkle"/></svg><span class="c-lime">Support your colleagues and champion their purpose.</span>
      <svg class="star"><use href="#sparkle"/></svg><span class="c-lime">Learn something new each day.</span>
      <svg class="star"><use href="#sparkle"/></svg><span class="c-teal">Trust your knowledge and seek advice only from respected sources.</span>
      <svg class="star"><use href="#sparkle"/></svg><span class="c-ink">Be a lifelong learner.</span>
      <svg class="star"><use href="#sparkle"/></svg><span class="c-green">Celebrate, respect and value the diversity of your culture.</span>
      <svg class="star"><use href="#sparkle"/></svg><span class="c-lime">Respond to distress with random acts of kindness.</span>
      <svg class="star"><use href="#sparkle"/></svg><span class="c-green">Smile and infect others with your happiness.</span>
      <svg class="star"><use href="#sparkle"/></svg><span class="c-ink manifesto__big">Have fun!</span>
      <svg class="star"><use href="#sparkle"/></svg><span class="c-green">Always do the right thing without exception.</span>
      <svg class="star"><use href="#sparkle"/></svg><span class="c-lime">You are unique, revel in your individuality.</span>
      <svg class="star"><use href="#sparkle"/></svg><span class="c-teal">Don’t ever believe you’ve arrived, keep going.</span>
      <svg class="star"><use href="#sparkle"/></svg><span class="c-ink">Always be solution focused.</span>
      <svg class="star"><use href="#sparkle"/></svg><span class="c-green">Seek success, firstly from within.</span>
      <svg class="star"><use href="#sparkle"/></svg><span class="c-teal">Only follow exceptional leaders.</span>
      <svg class="star"><use href="#sparkle"/></svg><span class="c-lime">If there’s no one left to follow, then lead!</span>
      <svg class="star"><use href="#sparkle"/></svg><span class="c-green">Always lead with purpose, passion and commitment.</span>
      <svg class="star"><use href="#sparkle"/></svg><span class="c-lime">Respond to complex situations <span class="u">innovatively</span>, creatively and safely within the scope of your practice.</span>
      <svg class="star"><use href="#sparkle"/></svg><span class="c-green">Adopt a ‘can do’ attitude to anything that comes your way.</span>
      <svg class="star"><use href="#sparkle"/></svg><span class="c-ink">Choose your thoughts wisely, they create your reality.</span>
    </p>

    <p class="closing"><svg class="star"><use href="#sparkle"/></svg>Live your dream.</p>
  </section>

  <div class="partner-badge">
    <span class="partner-badge__name">CalmPeak</span>
  </div>
</main>
</body>
</html>
```